New hardcover book cover

I want a striking, eye-catching cover with title, subtitle and a picture.See for previous book covers: www.brightquillpress.com

Target Market(s)

young, successful entrepreneurs that have built a business in a niche market that they discovered.

Font styles to use
Serif

Colors

Designer to choose colors to be used in the design.

Requirements
Must have
• A book cover that impresses and captures the imagination of those who look at it.
• MY MISTAKE, SORRY.
• Title: Founders Behind the Quiet Trade Boom
• Subtitle: 25 stories of success from
• discovering hidden opportunities
• Author: Dennis Harlow
• Please use the photo attached, thanks.

```html
<!DOCTYPE html>
<html lang="en">
<head>
<meta charset="utf-8">
<title>Founders Behind the Quiet Trade Boom — Dennis Harlow</title>
<link rel="stylesheet" href="https://fonts.googleapis.com/css2?family=Cinzel:wght@400&family=Josefin+Sans:wght@300&display=swap">
<style>
  :root {
    --cover-dark: #363432;
    --title-light: #ffffff;
    --title-accent: #e9b98b;
    --rule-red: #e3221f;
    --photo-dark: #262626;
    --photo-mid: #8f8d89;
    --photo-light: #d8d5cf;
    --wood: #b98552;
    --subtitle: #cfcac3;
  }
  * { margin: 0; padding: 0; box-sizing: border-box; }
  html, body { width: 765px; height: 1200px; overflow: hidden; background: var(--cover-dark); }
  .book-cover {
    position: relative;
    width: 765px;
    height: 1200px;
    background: var(--cover-dark);
    overflow: hidden;
  }
  .cover-photo {
    position: absolute;
    left: 0; top: 0;
    width: 765px; height: 576px;
    background: linear-gradient(105deg, var(--photo-dark) 0%, var(--photo-mid) 35%, var(--photo-light) 50%, var(--photo-mid) 68%, var(--wood) 100%);
  }
  .accent-rule {
    position: absolute;
    left: 506px; top: 572px;
    width: 259px; height: 6px;
    background: var(--rule-red);
  }
  .title-block {
    font-family: "Cinzel", serif;
    font-weight: 400;
    text-transform: uppercase;
  }
  .title-line {
    position: absolute;
    left: 0; right: 0;
    text-align: center;
    line-height: 1;
    white-space: nowrap;
  }
  .title-lead {
    top: 664px;
    color: var(--title-light);
    font-size: 60px;
  }
  .title-pair {
    top: 726px;
    color: var(--title-light);
    display: flex;
    justify-content: center;
    align-items: flex-end;
    gap: 10px;
  }
  .title-small { font-size: 32px; padding-bottom: 6px; }
  .title-mid { font-size: 86px; }
  .title-accent {
    color: var(--title-accent);
    font-size: 100px;
    letter-spacing: 2px;
  }
  .title-accent.first { top: 808px; }
  .title-accent.second { top: 898px; }
  .subtitle {
    position: absolute;
    left: 0; right: 0; top: 1018px;
    text-align: center;
    font-family: "Josefin Sans", sans-serif;
    font-weight: 300;
    font-size: 22px;
    letter-spacing: 1px;
    color: var(--subtitle);
  }
  .author {
    position: absolute;
    left: 0; right: 0; top: 1086px;
    text-align: center;
    font-family: "Josefin Sans", sans-serif;
    font-weight: 300;
    font-size: 36px;
    letter-spacing: 8px;
    color: var(--title-light);
    text-transform: uppercase;
  }
</style>
</head>
<body>
  <main class="book-cover">
    <div class="cover-photo" role="img" aria-label="Photo of a dart hitting the bullseye of a dartboard"></div>
    <div class="accent-rule"></div>
    <h1 class="title-block">
      <span class="title-line title-lead">Founders Behind</span>
      <span class="title-line title-pair">
        <span class="title-small">The</span>
        <span class="title-mid">Quiet</span>
      </span>
      <span class="title-line title-accent first">Trade</span>
      <span class="title-line title-accent second">Boom</span>
    </h1>
    <p class="subtitle">25 stories of success from discovering hidden opportunities</p>
    <p class="author">Dennis Harlow</p>
  </main>
</body>
</html>
```